Building company buisness cards

We are looking for a sharp modern new look for our business cards.
We are a New Zealand based company that specialises in house and land packages.
We have attached a photo of the current logo and would like to see if it can be improved somehow if needed.
We are open to any colours but we have chosen green at this stage.
Feel free to change the font and make the logo smarter looking.
Play with the colours and see what looks best.

We want a card that looks so good know one will want to throw it away!

Target Market(s)

Home buyers

Industry/Entity Type

Building

Contact Information for Business Card

Derek Tolvane
0217394062
dtolvane@quillmarkhomesteads.co.nz
quillmarkhomesteads.co.nz

Font styles to use
Serif
Sans Serif

Colors

Designer to choose colors to be used in the design.

Requirements
Must have
• Logo and company name on one side, details on the other side
Nice to have
• Color codes for the original green are HEX #4a8028, RGB(74,128,40), CMYK(42,0,69,50)
• Round corners, Raised and/or spot UV

```html
<!DOCTYPE html>
<html lang="en">
<head>
<meta charset="utf-8">
<title>Quillmark Homesteads – Business Cards</title>
<link rel="stylesheet" href="https://fonts.googleapis.com/css2?family=Noto+Sans:wght@400;700&display=swap">
<style>
  :root {
    --brand-green: #4a8028;
    --brand-green-deep: #437524;
    --card-white: #ffffff;
    --ink: #111111;
    --ink-muted: #5b5b5b;
    --rule: #222222;
    --backdrop: #e9e6df;
  }
  * { box-sizing: border-box; margin: 0; padding: 0; }
  html, body {
    width: 1200px;
    height: 1200px;
    overflow: hidden;
    background: var(--backdrop);
    font-family: "Noto Sans", Verdana, sans-serif;
  }
  .canvas {
    position: relative;
    width: 1200px;
    height: 1200px;
  }
  .card {
    position: absolute;
    width: 878px;
    height: 516px;
    overflow: hidden;
  }

  /* Details side */
  .card-details {
    left: 17px;
    top: 58px;
    background: var(--card-white);
  }
  .card-details .base-band {
    position: absolute;
    left: 0; right: 0; bottom: 0;
    height: 12px;
    background: var(--brand-green);
  }
  .person-name {
    position: absolute;
    top: 118px;
    width: 100%;
    text-align: center;
    font-size: 38px;
    font-weight: 400;
    letter-spacing: 1px;
    color: var(--brand-green);
  }
  .person-role {
    position: absolute;
    top: 174px;
    width: 100%;
    text-align: center;
    font-size: 19px;
    letter-spacing: 0.5px;
    color: var(--ink-muted);
  }
  .contact-divider {
    position: absolute;
    top: 262px;
    left: 0;
    width: 100%;
    display: flex;
    justify-content: center;
    align-items: center;
    gap: 12px;
  }
  .contact-divider .rule {
    width: 82px;
    height: 2px;
    background: var(--rule);
  }
  .contact-divider .icons {
    display: flex;
    gap: 12px;
    align-items: center;
  }
  .contact-list {
    position: absolute;
    top: 302px;
    width: 100%;
    text-align: center;
    font-size: 22px;
    line-height: 33px;
    color: var(--ink);
  }

  /* Brand side */
  .card-brand {
    left: 295px;
    top: 626px;
    background: var(--brand-green);
  }
  .brand-field {
    position: absolute;
    left: 0; top: 0;
    width: 100%;
    height: 497px;
    background: linear-gradient(180deg, var(--brand-green) 0%, var(--brand-green-deep) 100%);
  }
  .brand-name {
    position: absolute;
    top: 208px;
    width: 100%;
    text-align: center;
    font-size: 44px;
    font-weight: 700;
    line-height: 48px;
    color: var(--card-white);
    display: flex;
    justify-content: center;
    align-items: center;
    gap: 18px;
  }
  .brand-name .mark-dot {
    width: 18px;
    height: 18px;
    border-radius: 50%;
    background: var(--card-white);
  }
  .brand-url-strip {
    position: absolute;
    left: 0; right: 0; bottom: 0;
    height: 19px;
    background: var(--card-white);
    text-align: center;
    font-size: 19px;
    line-height: 22px;
    color: var(--ink);
    overflow: hidden;
  }
</style>
</head>
<body>
<main class="canvas">

  <section class="card card-details" aria-label="Business card, contact side">
    <h1 class="person-name">DEREK TOLVANE</h1>
    <p class="person-role">Managing Director</p>

    <div class="contact-divider">
      <span class="rule"></span>
      <span class="icons">
        <svg width="26" height="24" viewBox="0 0 26 24" aria-label="Phone">
          <path d="M2 9 Q13 1 24 9 L21 12 L18 10 L18 7 Q13 5 8 7 L8 10 L5 12 Z" fill="#4a8028"/>
          <path d="M6 13 L9 10 L17 10 L20 13 L21 22 L5 22 Z" fill="#4a8028"/>
          <circle cx="13" cy="16" r="3" fill="#fff"/>
        </svg>
        <svg width="34" height="24" viewBox="0 0 34 24" aria-label="Email">
          <rect x="1" y="2" width="32" height="20" fill="#4a8028"/>
          <path d="M2 3 L17 14 L32 3 M2 21 L13 11 M32 21 L21 11" stroke="#fff" stroke-width="1.8" fill="none"/>
        </svg>
        <svg width="26" height="26" viewBox="0 0 26 26" aria-label="Website">
          <g fill="none" stroke="#4a8028" stroke-width="2">
            <circle cx="13" cy="13" r="11"/>
            <ellipse cx="13" cy="13" rx="5" ry="11"/>
            <path d="M2 13 H24 M4 7 H22 M4 19 H22"/>
          </g>
        </svg>
      </span>
      <span class="rule"></span>
    </div>

    <address class="contact-list" style="font-style: normal;">
      0217394062<br>
      dtolvane@quillmarkhomesteads.co.nz<br>
      www.quillmarkhomesteads.co.nz
    </address>

    <div class="base-band"></div>
  </section>

  <section class="card card-brand" aria-label="Business card, brand side">
    <div class="brand-field" role="img" aria-label="Green field with a faint repeating pattern of houses and families"></div>
    <p class="brand-name"><span class="mark-dot"></span>quillmark homesteads.</p>
    <p class="brand-url-strip">www.quillmarkhomesteads.co.nz</p>
  </section>

</main>
</body>
</html>
```